Clean business card with logo provided

I want a card that will stand out among the masses. I need the color and image to show professionalism and yet have a family appeal showing that I only deal with win/win scenarios. The back of the card will be used to take notes about the individual so I can use that in my database entry. I like modern design but need professionalism in it also. It needs to fit my "clean, safe, and affordable housing" motto. I need to be able to write on the file and update the card details for my employees.

Target Market(s)

Investors looking to make investment income through real estate

Industry/Entity Type

Real Estate

Contact Information for Business Card

Brent Kovalich
blank address, city, st, zip code
480-555-3174
brentkovalich@ridgeworthrentals.example
www.ridgeworthrentals.example

Font styles to use
Sans Serif

Requirements
Must have
• I would like the back of the card to have lines for info. example
• Met/Visited: Date:
• Interets:
Nice to have
• I want the cards color to match the logo background color. Font with details to be san serif and black. I want the card rectangular with square corners. Standard business card size. I would like to see cards designed with both images to see which i prefer more.

```html
<!DOCTYPE html>
<html lang="en">
<head>
<meta charset="UTF-8">
<title>Ridgeworth Rentals LLC — Business Card</title>
<link href="https://fonts.googleapis.com/css2?family=Cinzel:wght@400&family=Open+Sans:wght@400&display=swap" rel="stylesheet">
<style>
  :root {
    --page: #8f9091;
    --card-black: #000000;
    --card-paper: #e9eaec;
    --teal: #1c9db3;
    --light-text: #d2d2d2;
    --divider: #555555;
    --rule: #1a1a1a;
  }
  * { margin: 0; padding: 0; box-sizing: border-box; }
  html, body {
    width: 1105px; height: 1200px; overflow: hidden;
    background: var(--page);
  }
  .canvas { position: relative; width: 1105px; height: 1200px; }
  .card {
    position: absolute; left: 182px; width: 746px; height: 426px;
    overflow: hidden;
  }
  .card--front { top: 119px; background: var(--card-black); }
  .card--back { top: 637px; background: var(--card-paper); }

  .brand { position: absolute; text-align: center; }
  .brand__name {
    font-family: "Cinzel", serif; font-weight: 400; color: var(--teal);
    letter-spacing: 0.05em; white-space: nowrap; line-height: 1;
  }
  .brand__tagline {
    font-family: "Open Sans", sans-serif; color: var(--teal); line-height: 1;
    white-space: nowrap;
  }
  .card--front .brand { left: 22px; top: 178px; width: 290px; }
  .card--front .brand__name { font-size: 18px; }
  .card--front .brand__tagline { font-size: 9.5px; margin-top: 10px; }

  .divider {
    position: absolute; left: 330px; top: 130px; width: 1px; height: 193px;
    background: linear-gradient(to bottom, transparent, var(--divider) 20%, var(--divider) 80%, transparent);
  }

  .contact { position: absolute; left: 356px; top: 128px; right: 16px; font-family: "Open Sans", sans-serif; }
  .contact__name {
    font-family: "Cinzel", serif; font-weight: 400; color: var(--teal); font-size: 26px;
    letter-spacing: 0.03em; line-height: 1; white-space: nowrap;
  }
  .contact__address { margin-top: 20px; color: var(--light-text); font-size: 18px; line-height: 26px; }
  .contact__list { list-style: none; margin-top: 12px; }
  .contact__item {
    display: flex; align-items: center; gap: 10px; white-space: nowrap;
    color: var(--light-text); font-size: 16px; line-height: 28px;
  }
  .contact__icon { width: 16px; height: 16px; flex: none; fill: var(--teal); }

  .back-band {
    position: absolute; left: 0; top: 0; width: 100%; height: 180px;
    background: var(--card-black);
  }
  .card--back .brand { left: 0; top: 52px; width: 100%; }
  .card--back .brand__name { font-size: 36px; }
  .card--back .brand__tagline { font-size: 12px; margin-top: 14px; }

  .notes { position: absolute; left: 55px; top: 218px; width: 624px; }
  .notes__row {
    display: flex; align-items: flex-end; height: 51px;
    font-family: "Open Sans", sans-serif; font-size: 19px; color: var(--teal);
  }
  .notes__row:first-child { height: 28px; }
  .notes__label { white-space: nowrap; line-height: 1; padding-right: 4px; }
  .notes__line { flex: 1; border-bottom: 1.5px solid var(--rule); margin-bottom: 1px; }
</style>
</head>
<body>
<main class="canvas">
  <section class="card card--front" aria-label="Business card front">
    <div class="brand">
      <p class="brand__name">RIDGEWORTH RENTALS LLC</p>
      <p class="brand__tagline">Providing clean, safe, and affordable housing</p>
    </div>
    <div class="divider"></div>
    <div class="contact">
      <h1 class="contact__name">BRENT KOVALICH</h1>
      <p class="contact__address">4120 Alder Court<br>Fairbanks, Alaska 99701</p>
      <ul class="contact__list">
        <li class="contact__item">
          <svg class="contact__icon" viewBox="0 0 24 24" aria-hidden="true"><path d="M6.6 10.8a15.1 15.1 0 0 0 6.6 6.6l2.2-2.2a1 1 0 0 1 1-.25 11.4 11.4 0 0 0 3.6.57 1 1 0 0 1 1 1V20a1 1 0 0 1-1 1A17 17 0 0 1 3 4a1 1 0 0 1 1-1h3.5a1 1 0 0 1 1 1c0 1.25.2 2.45.57 3.57a1 1 0 0 1-.25 1z"/></svg>
          480-555-3174
        </li>
        <li class="contact__item">
          <svg class="contact__icon" viewBox="0 0 24 24" aria-hidden="true"><path d="M2 5h20v14H2z M3.5 6.5v.4l8.5 5.6 8.5-5.6v-.4z" fill-rule="evenodd"/></svg>
          brentkovalich@ridgeworthrentals.example
        </li>
        <li class="contact__item">
          <svg class="contact__icon" viewBox="0 0 24 24" aria-hidden="true"><circle cx="12" cy="12" r="10"/><path d="M2 12h20M12 2c3 3 3 17 0 20M12 2c-3 3-3 17 0 20" stroke="#000" stroke-width="1.4" fill="none"/></svg>
          www.ridgeworthrentals.example
        </li>
      </ul>
    </div>
  </section>

  <section class="card card--back" aria-label="Business card back">
    <div class="back-band"></div>
    <div class="brand">
      <p class="brand__name">RIDGEWORTH RENTALS LLC</p>
      <p class="brand__tagline">Providing clean, safe, and affordable housing</p>
    </div>
    <div class="notes">
      <div class="notes__row"><span class="notes__label">MET/VISITED:</span><span class="notes__line"></span></div>
      <div class="notes__row"><span class="notes__label">DATE:</span><span class="notes__line"></span></div>
      <div class="notes__row"><span class="notes__label">INTERESTS:</span><span class="notes__line"></span></div>
      <div class="notes__row"><span class="notes__line"></span></div>
    </div>
  </section>
</main>
</body>
</html>
```